Business Card Design for BrightvaleMedia.com

--I need a business card design for my company BrightvaleMedia.com

I have attached my logo...I want the brightvale media logo on the front of the business card, and then I want The Quillstone Chief on the back of it with my information.

I would like to see a light colored background as well as a dark colored background

FRONT:
BRIGHTVALE MEDIA LOGO
248 N. Larkmoor
3rd Floor
San Diego CA 92173
www.BrightvaleMedia.com

Advanced Website & App Development
Websites, Apps, Online Voucher Systems

Leading Edge Marketing Services
SMS, VB, SMM, SEM,

BACK:
QUILLSTONE CHIEF LOGO
Dorian Pelletta
The Quillstone Chief
Call Or Text: 619-555-0148
Dorian@QuillstoneChief.example
www.QuillstoneChief.example

Target Market(s)

small business owners

Industry/Entity Type

Business Consultant

Contact Information for Business Card

FRONT:
BRIGHTVALE MEDIA LOGO
248 N. Larkmoor
3rd Floor
San Diego CA 92173
www.BrightvaleMedia.com

SMS, VB, SMM, SEM,

BACK:
QUILLSTONE CHIEF LOGO
Dorian Pelletta
The Quillstone Chief
Dorian@QuillstoneChief.example
www.QuillstoneChief.example

Requirements
Must have
• add this quote on it somewhere, anywhere,preferrably on back
• "The Fastest Way To Success Is To Take Action”
• — Dorian Pelletta, Quillstone Chief
Nice to have
• open
Should not have
• red

```html
<!DOCTYPE html>
<html lang="en">
<head>
<meta charset="utf-8">
<title>Brightvale Media – Business Card</title>
<link rel="stylesheet" href="https://fonts.googleapis.com/css2?family=Source+Sans+3:ital,wght@0,400;0,600;0,700;1,400&display=swap">
<style>
  :root {
    --backdrop: #3a3a3a;
    --brand-blue: #0a73ad;
    --card-white: #ffffff;
    --ink-grey: #555555;
    --ink-dark: #3d3d3d;
    --rule-blue: #2a7fb2;
    --shadow: rgba(0, 0, 0, 0.45);
  }
  * { box-sizing: border-box; margin: 0; padding: 0; }
  html, body {
    width: 1105px;
    height: 1200px;
    overflow: hidden;
  }
  body {
    background: var(--backdrop);
    font-family: "Source Sans 3", "Myriad Pro", sans-serif;
    position: relative;
  }
  .card {
    position: absolute;
    left: 196px;
    width: 719px;
    height: 410px;
    box-shadow: 0 4px 10px var(--shadow);
  }
  .card--front {
    top: 146px;
    background: var(--brand-blue);
    color: var(--card-white);
  }
  .card--back {
    top: 602px;
    background: var(--card-white);
    color: var(--ink-grey);
  }

  /* Front */
  .brand-name {
    position: absolute;
    left: 59px;
    top: 62px;
    font-weight: 600;
    font-size: 40px;
    line-height: 1;
    letter-spacing: 3px;
    text-transform: uppercase;
    color: var(--card-white);
  }
  .front-details {
    position: absolute;
    left: 59px;
    top: 140px;
    font-size: 19.5px;
    line-height: 27px;
  }
  .front-details p + p { margin-top: 12px; }
  .front-details .web { font-weight: 700; }

  /* Back */
  .chief-name {
    position: absolute;
    right: 42px;
    top: 60px;
    font-weight: 600;
    font-size: 38px;
    line-height: 1;
    letter-spacing: 2px;
    text-transform: uppercase;
    color: var(--brand-blue);
  }
  .motto {
    position: absolute;
    right: 42px;
    top: 126px;
    text-align: right;
    color: var(--ink-grey);
  }
  .motto-text {
    font-size: 18px;
    font-style: italic;
    line-height: 24px;
  }
  .motto-source {
    font-size: 15px;
    line-height: 22px;
    margin-top: 2px;
  }
  .person {
    position: absolute;
    left: 40px;
    top: 244px;
  }
  .person-name {
    font-size: 27px;
    font-weight: 600;
    color: var(--brand-blue);
    line-height: 1.1;
  }
  .person-title {
    font-size: 20px;
    color: var(--ink-grey);
    margin-top: 2px;
  }
  .divider {
    position: absolute;
    left: 40px;
    right: 42px;
    top: 308px;
    height: 1.5px;
    background: var(--rule-blue);
  }
  .contact-list {
    position: absolute;
    left: 40px;
    top: 321px;
    list-style: none;
    font-size: 19px;
    line-height: 27px;
    color: var(--ink-grey);
  }
  .contact-list li {
    display: flex;
    align-items: center;
    gap: 10px;
  }
  .contact-list svg { width: 17px; height: 17px; flex: none; }
  .website {
    position: absolute;
    right: 42px;
    top: 348px;
    font-size: 19.5px;
    font-weight: 700;
    color: var(--ink-dark);
    line-height: 27px;
  }
</style>
</head>
<body>

<section class="card card--front" aria-label="Card front">
  <div class="brand-name">Brightvale Media</div>
  <div class="front-details">
    <p>248 N. Larkmoor, 3rd Floor<br>San Diego CA 92173<br><span class="web">www.BrightvaleMedia.com</span></p>
    <p>Advanced Website &amp; App Development<br>Websites • Apps • Online Voucher Systems</p>
    <p>Leading Edge Marketing Services<br>SMS • VB • SMM • SEM</p>
  </div>
</section>

<section class="card card--back" aria-label="Card back">
  <div class="chief-name">Quillstone Chief</div>
  <blockquote class="motto">
    <p class="motto-text">“The Fastest Way To Success Is To Take Action”</p>
    <p class="motto-source">— Dorian Pelletta, Quillstone Chief</p>
  </blockquote>
  <div class="person">
    <div class="person-name">Dorian Pelletta</div>
    <div class="person-title">The Quillstone Chief</div>
  </div>
  <div class="divider"></div>
  <ul class="contact-list">
    <li>
      <svg viewBox="0 0 24 24" aria-hidden="true"><path fill="#0a73ad" d="M6.6 10.8c1.4 2.8 3.8 5.1 6.6 6.6l2.2-2.2c.3-.3.7-.4 1-.2 1.1.4 2.3.6 3.6.6.6 0 1 .4 1 1V20c0 .6-.4 1-1 1C10.6 21 3 13.4 3 4c0-.6.4-1 1-1h3.5c.6 0 1 .4 1 1 0 1.3.2 2.5.6 3.6.1.3 0 .7-.2 1z"/></svg>
      <span>619-555-0148</span>
    </li>
    <li>
      <svg viewBox="0 0 24 24" aria-hidden="true"><path fill="#0a73ad" d="M2 5h20v14H2z"/><path fill="none" stroke="#fff" stroke-width="1.8" d="M2.5 5.5 12 13l9.5-7.5"/></svg>
      <span>Dorian@QuillstoneChief.example</span>
    </li>
  </ul>
  <div class="website">www.QuillstoneChief.example</div>
</section>

</body>
</html>
```